Business card design for holistic health care clinic

We need a double-sided business card design for our holistic health care clinic that integrates our logo design and also its color scheme. My business is called Valmira. It is an integrative medicine clinic. You have already done the logo for me. Please ensure an elegant and upscale design that is not cluttered, but still has all the necessary information (please see below for details).

Target Market(s)

Wellness, fitness, rehabilitation for educated, well-traveled open-minded clients who are focused on natural, organic, balanced and preventive healthcare and lifestyle.

Industry/Entity Type

Medical

Contact Information for Business Card

Modern, clean.

Number of Pages Required

1 page

Font styles to use
Serif
Sans Serif

Colors

Designer to choose colors to be used in the design.

Requirements
Must have
• Logo on one side, all other information on the other side.
• Other information should include:
• Tobias Wrenfeld - DOE, CPT, LMT
• 4100 East Marrow Drive
• Austin, TX 78119
• 512 555 0148
• 818 555 0192
• info@ValmiraHealth.example
• t.wrenfeld@ValmiraHealth.example
Nice to have
• Darker background on front - but not totally black - shaded/dark gray.

```html
<!DOCTYPE html>
<html lang="en">
<head>
<meta charset="utf-8">
<title>Valmira – Business Card</title>
<link rel="stylesheet" href="https://fonts.googleapis.com/css2?family=Roboto:ital,wght@0,400;0,500;0,700;1,400&family=Roboto+Condensed:ital,wght@0,400;0,700;1,400&display=swap">
<style>
  :root {
    --backdrop: #5b4838;
    --card-dark: #242424;
    --brand-blue: #0a8ac6;
    --wave-grey: #a9a9a9;
    --wave-edge: #1a1a1a;
    --card-light: #f3f3f3;
    --text-light: #ffffff;
    --text-muted: #555555;
    --rule: #8a8a8a;
  }
  * { margin: 0; padding: 0; box-sizing: border-box; }
  html, body { width: 1200px; height: 960px; overflow: hidden; }
  body {
    background: var(--backdrop);
    position: relative;
    font-family: "Roboto", Arial, sans-serif;
  }
  .card {
    position: absolute;
    width: 600px;
    height: 343px;
    border-radius: 20px;
    overflow: hidden;
  }
  .card-front { left: 314px; top: 113px; background: var(--card-dark); }
  .card-back { left: 311px; top: 472px; background: var(--card-light); }

  .front-wave { position: absolute; inset: 0; }

  .brand-name {
    font-family: "Roboto", Arial, sans-serif;
    font-weight: 700;
    color: var(--brand-blue);
    letter-spacing: 1px;
    line-height: 1;
  }
  .brand-tagline {
    font-family: "Roboto", Arial, sans-serif;
    font-weight: 500;
    color: var(--brand-blue);
    line-height: 1;
  }
  .front-brand { position: absolute; left: 39px; top: 82px; }
  .front-brand .brand-name { font-size: 50px; }
  .front-brand .brand-tagline { font-size: 15.5px; margin-top: 8px; margin-left: 4px; }

  .holder {
    position: absolute;
    left: 39px;
    top: 276px;
    color: var(--text-light);
    font-family: "Roboto Condensed", Arial, sans-serif;
    font-weight: 700;
    font-size: 21px;
    white-space: nowrap;
  }
  .holder-credentials { font-size: 12px; margin-left: 3px; }

  .contact {
    position: absolute;
    right: 32px;
    top: 202px;
    text-align: right;
    color: var(--text-light);
    font-size: 14.5px;
    line-height: 19.5px;
  }
  .contact-address { margin-bottom: 7px; }
  .contact-row { display: flex; justify-content: flex-end; align-items: center; gap: 6px; }
  .contact-row svg { width: 13px; height: 13px; flex: none; }
  .contact-address-line { padding-right: 0; }

  .back-brand {
    position: absolute;
    left: 0; right: 0; top: 148px;
    text-align: center;
  }
  .back-brand .brand-name { font-size: 62px; }
  .back-brand .brand-tagline { font-size: 18.5px; margin-top: 10px; }

  .motto {
    position: absolute;
    left: 85px; right: 85px; top: 272px;
    display: flex; align-items: center; gap: 6px;
    font-family: "Roboto Condensed", Arial, sans-serif;
    font-style: italic;
    font-size: 18px;
    color: var(--text-muted);
    white-space: nowrap;
  }
  .motto-rule { flex: 1; height: 1px; background: linear-gradient(to right, transparent, var(--rule)); }
  .motto-rule.right { background: linear-gradient(to left, transparent, var(--rule)); }
</style>
</head>
<body>
  <section class="card card-front" aria-label="Business card front">
    <svg class="front-wave" viewBox="0 0 600 343" preserveAspectRatio="none" aria-hidden="true">
      <path d="M150 236 C260 226 360 150 470 150 C530 150 570 170 600 190 L600 343 L0 343 Z" fill="var(--wave-grey)"/>
      <path d="M0 178 C50 220 100 240 160 238 C280 234 360 160 470 158 C530 157 570 185 600 207 L600 343 L0 343 Z" fill="var(--brand-blue)"/>
      <path d="M0 178 C50 220 100 240 160 238 C280 234 360 160 470 158 C530 157 570 185 600 207" fill="none" stroke="var(--wave-edge)" stroke-width="2"/>
    </svg>

    <div class="front-brand">
      <div class="brand-name">VALMIRA</div>
      <div class="brand-tagline">Integrative Holistic Medicine</div>
    </div>

    <div class="holder">TOBIAS WRENFELD<span class="holder-credentials"> - DOE, CPT, LMT</span></div>

    <div class="contact">
      <div class="contact-address">
        <div>4100 East Marrow Drive</div>
        <div>Austin, TX 78119</div>
      </div>
      <div class="contact-row"><span>512 555 0148</span>
        <svg viewBox="0 0 16 16"><path fill="#fff" d="M3.5 1 L6 1.5 L7 5 L5.3 6.3 C6.2 8.2 7.8 9.8 9.7 10.7 L11 9 L14.5 10 L15 12.5 C15 14 13.8 15 12.5 15 C6.7 15 1 9.3 1 3.5 C1 2.2 2 1 3.5 1 Z"/></svg>
      </div>
      <div class="contact-row"><span>818 555 0192</span>
        <svg viewBox="0 0 16 16"><rect x="4" y="0.8" width="8" height="14.4" rx="1.5" fill="none" stroke="#fff" stroke-width="1.5"/><circle cx="8" cy="12.6" r="0.9" fill="#fff"/></svg>
      </div>
      <div class="contact-row"><span>t.wrenfeld@ValmiraHealth.example</span>
        <svg viewBox="0 0 16 16"><rect x="1" y="3.5" width="14" height="9.5" fill="#fff"/><path d="M1 3.5 L8 9 L15 3.5" fill="none" stroke="var(--brand-blue)" stroke-width="1.2"/></svg>
      </div>
      <div class="contact-row"><span>www.ValmiraHealth.example</span>
        <svg viewBox="0 0 16 16"><circle cx="8" cy="8" r="6.8" fill="#fff"/><ellipse cx="8" cy="8" rx="3" ry="6.8" fill="none" stroke="var(--brand-blue)" stroke-width="1"/><path d="M1.2 8 H14.8" stroke="var(--brand-blue)" stroke-width="1"/></svg>
      </div>
    </div>
  </section>

  <section class="card card-back" aria-label="Business card back">
    <div class="back-brand">
      <div class="brand-name">VALMIRA</div>
      <div class="brand-tagline">Integrative Holistic Medicine</div>
    </div>
    <div class="motto">
      <span class="motto-rule"></span>
      <span>helping the body help itself</span>
      <span class="motto-rule right"></span>
    </div>
  </section>
</body>
</html>
```